Commercial Loan Originator Business Card (CHANGE COLORS SCHEME)

CHANGE COLOR SCHEME - SAME DESIGN

Name Marlene Agate
Title Commercial Loan Originator
Office (800) 417-2906 x68
Direct (240) 615-2043
Email freshgreens4life@quillbox.example

Name Dale Morrow
Office (800) 417-2906 x70
Direct (410) 392-5184
Email d.morthehomeguy@quillbox.example

Name Leonard Vasko
Office (800) 417-2906 x71
Direct (215) 463-0712
Email l.vasko41@quillbox.example

Name Gwen Halsey
Office (800) 417-2906 x
Direct (202) 548-1370
Email ghalsey63@quillbox.example

Name Mirna Ashby
Office (800) 417-2906 x72
Direct (240) 871-4526
Email tristatehomelending@quillbox.example

```html
<!DOCTYPE html>
<html lang="en">
<head>
<meta charset="utf-8">
<title>Commercial Loan Originator Business Cards</title>
<link rel="stylesheet" href="https://fonts.googleapis.com/css2?family=Montserrat:wght@400;500;700&display=swap">
<style>
  :root {
    --accent: #0f6e78;
    --accent-soft: #2a9aa3;
    --ink: #2b3238;
    --card: #ffffff;
    --bg-top: #d0d0d0;
    --bg-bottom: #9d9d9d;
  }
  * { box-sizing: border-box; margin: 0; padding: 0; }
  html, body { width: 1200px; height: 1194px; overflow: hidden; }
  body {
    position: relative;
    background: linear-gradient(180deg, var(--bg-top) 0%, var(--bg-bottom) 100%);
    font-family: "Montserrat", Arial, sans-serif;
    color: var(--ink);
  }
  .card {
    position: absolute;
    width: 509px;
    height: 291px;
    background: var(--card);
    border-radius: 26px;
    box-shadow: 3px 5px 10px rgba(0,0,0,0.28);
  }
  .card--leonard { left: 70px;  top: 95px; }
  .card--marlene { left: 620px; top: 98px; }
  .card--dale    { left: 70px;  top: 450px; }
  .card--gwen    { left: 620px; top: 453px; }
  .card--mirna   { left: 345px; top: 807px; }

  .portrait {
    position: absolute;
    left: 40px;
    top: 73px;
    width: 147px;
    height: 147px;
    border-radius: 50%;
    border: 2px solid var(--accent);
  }
  .portrait--navy  { background: radial-gradient(circle at 50% 40%, #6b4a3a 0%, #2a3550 55%, #3f6a8e 100%); }
  .portrait--pink  { background: radial-gradient(circle at 50% 35%, #7a4e3a 0%, #f3e9ee 45%, #e0358f 80%); }
  .portrait--olive { background: radial-gradient(circle at 50% 35%, #6a4a3a 0%, #5b5d4f 50%, #c9ccd0 100%); }
  .portrait--warm  { background: radial-gradient(circle at 50% 40%, #7a5040 0%, #4d5a3a 55%, #b86a5e 100%); }
  .portrait--brown { background: radial-gradient(circle at 50% 35%, #7a4e38 0%, #2a2422 55%, #a58463 100%); }

  .divider {
    position: absolute;
    left: 210px;
    top: 76px;
    width: 1.5px;
    height: 139px;
    background: var(--accent);
  }
  .details {
    position: absolute;
    left: 232px;
    top: 74px;
  }
  .name {
    font-weight: 700;
    font-size: 25px;
    line-height: 28px;
    color: var(--accent);
    text-transform: uppercase;
    letter-spacing: 0.2px;
    white-space: nowrap;
  }
  .title {
    font-size: 15px;
    line-height: 18px;
    letter-spacing: 0.2px;
    white-space: nowrap;
  }
  .contacts {
    list-style: none;
    margin-top: 22px;
  }
  .contact {
    display: flex;
    align-items: center;
    height: 27.5px;
    font-size: 15.5px;
    letter-spacing: 0.2px;
    white-space: nowrap;
  }
  .contact svg {
    width: 12px;
    height: 12px;
    margin-right: 6px;
    flex: none;
    fill: var(--accent-soft);
  }
  .contact--email { font-size: 11.5px; letter-spacing: 0; }
</style>
</head>
<body>
<svg width="0" height="0" style="position:absolute">
  <defs>
    <symbol id="icon-phone" viewBox="0 0 24 24"><path d="M6.6 10.8c1.4 2.8 3.8 5.1 6.6 6.6l2.2-2.2c.3-.3.7-.4 1-.2 1.1.4 2.3.6 3.6.6.6 0 1 .4 1 1V20c0 .6-.4 1-1 1C10.6 21 3 13.4 3 4c0-.6.4-1 1-1h3.5c.6 0 1 .4 1 1 0 1.3.2 2.5.6 3.6.1.3 0 .7-.2 1L6.6 10.8z"/></symbol>
    <symbol id="icon-mobile" viewBox="0 0 24 24"><path d="M7 1h10c1.1 0 2 .9 2 2v18c0 1.1-.9 2-2 2H7c-1.1 0-2-.9-2-2V3c0-1.1.9-2 2-2zm0 3v15h10V4H7zm5 16.2a1 1 0 100 2 1 1 0 000-2z"/></symbol>
    <symbol id="icon-mail" viewBox="0 0 24 24"><path d="M2 5h20v14H2V5zm2 2v.5l8 5 8-5V7H4zm0 2.8V17h16V9.8l-8 5-8-5z"/></symbol>
  </defs>
</svg>

<article class="card card--leonard">
  <div class="portrait portrait--navy" role="img" aria-label="Portrait photo of Leonard Vasko"></div>
  <div class="divider"></div>
  <div class="details">
    <h2 class="name">Leonard Vasko</h2>
    <p class="title">Commercial Loan Originator</p>
    <ul class="contacts">
      <li class="contact"><svg><use href="#icon-phone"/></svg>(800) 417-2906 x71</li>
      <li class="contact"><svg><use href="#icon-mobile"/></svg>(215) 463-0712</li>
      <li class="contact contact--email"><svg><use href="#icon-mail"/></svg>l.vasko41@quillbox.example</li>
    </ul>
  </div>
</article>

<article class="card card--marlene">
  <div class="portrait portrait--pink" role="img" aria-label="Portrait photo of Marlene Agate"></div>
  <div class="divider"></div>
  <div class="details">
    <h2 class="name">Marlene Agate</h2>
    <p class="title">Commercial Loan Originator</p>
    <ul class="contacts">
      <li class="contact"><svg><use href="#icon-phone"/></svg>(800) 417-2906 x68</li>
      <li class="contact"><svg><use href="#icon-mobile"/></svg>(240) 615-2043</li>
      <li class="contact contact--email"><svg><use href="#icon-mail"/></svg>freshgreens4life@quillbox.example</li>
    </ul>
  </div>
</article>

<article class="card card--dale">
  <div class="portrait portrait--olive" role="img" aria-label="Portrait photo of Dale Morrow"></div>
  <div class="divider"></div>
  <div class="details">
    <h2 class="name">Dale Morrow</h2>
    <p class="title">Commercial Loan Originator</p>
    <ul class="contacts">
      <li class="contact"><svg><use href="#icon-phone"/></svg>(800) 417-2906 x70</li>
      <li class="contact"><svg><use href="#icon-mobile"/></svg>(410) 392-5184</li>
      <li class="contact contact--email"><svg><use href="#icon-mail"/></svg>d.morthehomeguy@quillbox.example</li>
    </ul>
  </div>
</article>

<article class="card card--gwen">
  <div class="portrait portrait--warm" role="img" aria-label="Portrait photo of Gwen Halsey"></div>
  <div class="divider"></div>
  <div class="details">
    <h2 class="name">Gwen Halsey</h2>
    <p class="title">Commercial Loan Originator</p>
    <ul class="contacts">
      <li class="contact"><svg><use href="#icon-phone"/></svg>(800) 417-2906 x</li>
      <li class="contact"><svg><use href="#icon-mobile"/></svg>(202) 548-1370</li>
      <li class="contact contact--email"><svg><use href="#icon-mail"/></svg>ghalsey63@quillbox.example</li>
    </ul>
  </div>
</article>

<article class="card card--mirna">
  <div class="portrait portrait--brown" role="img" aria-label="Portrait photo of Mirna Ashby"></div>
  <div class="divider"></div>
  <div class="details">
    <h2 class="name">Mirna Ashby</h2>
    <p class="title">Commercial Loan Originator</p>
    <ul class="contacts">
      <li class="contact"><svg><use href="#icon-phone"/></svg>(800) 417-2906 x72</li>
      <li class="contact"><svg><use href="#icon-mobile"/></svg>(240) 871-4526</li>
      <li class="contact contact--email"><svg><use href="#icon-mail"/></svg>tristatehomelending@quillbox.example</li>
    </ul>
  </div>
</article>
</body>
</html>
```